Garlic Farm for Farm Sales/Restaurant sales

Need a professional, but appealing to agriculture world. We are selling 27 kinds of Organic Garlic from a farm in Simla,CO. I have uploaded logo and business information-we are going to need a template, because I will need to use it for four separate people.
-We are trying to appeal to Farm to table restaurants
-As well as growers/farmers

Target Market(s)

Agriculture Sales/Restaurants-Organic

Industry/Entity Type

Agriculture

Contact Information for Business Card

Want it to look more unique then your average kelto stock card- I want it to look amazing

Font styles to use
Sans Serif

Colors
0455a3
ec1f27
fbed22
ffffff

Requirements
Must have
• Just be creative
Nice to have
• Colorful
Should not have
• plain

```html
<!DOCTYPE html>
<html lang="en">
<head>
<meta charset="utf-8">
<title>Prairie Clove business card</title>
<link href="https://fonts.googleapis.com/css2?family=Tinos&display=swap" rel="stylesheet">
<style>
  :root {
    --navy: #1f3163;
    --red: #c01f2f;
    --yellow: #ffdb00;
    --white: #ffffff;
    --backdrop: #e9e6e1;
  }
  * { margin: 0; padding: 0; box-sizing: border-box; }
  html, body { width: 1200px; height: 902px; overflow: hidden; background: var(--backdrop); }
  body { font-family: "Tinos", "Times New Roman", serif; position: relative; }

  .card {
    position: absolute; top: 296px; width: 540px; height: 309px;
    overflow: hidden; box-shadow: 0 6px 18px rgba(0,0,0,.18);
  }
  .card--front { left: 40px; background: var(--white); }
  .card--back { left: 620px; background: var(--red); }

  /* front face */
  .front-band { position: absolute; left: 0; right: 0; height: 42px; background: var(--yellow); }
  .front-band--top { top: 0; }
  .front-band--bottom { bottom: 0; }
  .front-rule { position: absolute; left: 0; right: 0; height: 2px; background: var(--red); }
  .front-rule--top { top: 50px; }
  .front-rule--bottom { bottom: 50px; }
  .front-brand {
    position: absolute; left: 0; right: 0; top: 92px;
    display: flex; flex-direction: column; align-items: center; gap: 18px;
  }
  .brand-dot { width: 70px; height: 70px; border-radius: 50%; background: var(--red); }
  .front-wordmark { color: var(--navy); font-size: 34px; letter-spacing: 6px; }

  /* back face */
  .back-shapes { position: absolute; inset: 0; }
  .back-brand {
    position: absolute; left: 36px; top: 112px; width: 210px;
    display: flex; align-items: center; gap: 12px;
  }
  .back-brand .brand-dot { width: 44px; height: 44px; flex: none; }
  .back-wordmark { color: var(--navy); font-size: 30px; line-height: 1; }

  .contact {
    position: absolute; right: 24px; top: 22px; width: 220px;
    text-align: right; color: var(--white);
  }
  .contact-name { color: var(--navy); font-size: 25px; line-height: 1.05; }
  .contact-title { font-size: 16px; margin-bottom: 18px; }
  .contact-group { margin-bottom: 16px; }
  .contact-line {
    display: flex; justify-content: flex-end; align-items: center; gap: 6px;
    font-size: 13.5px; line-height: 1.35;
  }
  .contact-line svg { width: 12px; height: 12px; flex: none; }
  .contact-address { font-size: 13.5px; line-height: 1.3; }
</style>
</head>
<body>

<section class="card card--front" aria-label="Card front">
  <div class="front-band front-band--top"></div>
  <div class="front-rule front-rule--top"></div>
  <div class="front-brand">
    <div class="brand-dot"></div>
    <div class="front-wordmark">PRAIRIE CLOVE</div>
  </div>
  <div class="front-rule front-rule--bottom"></div>
  <div class="front-band front-band--bottom"></div>
</section>

<section class="card card--back" aria-label="Card back">
  <svg class="back-shapes" viewBox="0 0 540 309" width="540" height="309" aria-hidden="true">
    <polygon points="0,0 238,0 322,112 278,309 0,309" fill="var(--navy)"/>
    <polygon points="0,0 212,0 294,112 254,309 0,309" fill="var(--yellow)"/>
  </svg>

  <div class="back-brand">
    <div class="brand-dot"></div>
    <div class="back-wordmark">Prairie Clove</div>
  </div>

  <div class="contact">
    <div class="contact-name">Employee Name</div>
    <div class="contact-title">Employee title</div>

    <div class="contact-group">
      <div class="contact-line">Name@ridgeclove.com
        <svg viewBox="0 0 12 12"><rect x="1" y="3" width="10" height="7" fill="none" stroke="#fff"/><path d="M1 3l5 4 5-4" fill="none" stroke="#fff"/></svg>
      </div>
      <div class="contact-line">www.ridgeclove.com
        <svg viewBox="0 0 12 12"><circle cx="6" cy="6" r="5" fill="none" stroke="#fff"/><path d="M1 6h10M6 1c-3 3-3 7 0 10M6 1c3 3 3 7 0 10" fill="none" stroke="#fff" stroke-width=".8"/></svg>
      </div>
    </div>

    <div class="contact-group">
      <div class="contact-line">+1 (555) 010 200
        <svg viewBox="0 0 12 12"><rect x="3" y="1" width="6" height="10" rx="1" fill="none" stroke="#fff"/><circle cx="6" cy="9" r=".8" fill="#fff"/></svg>
      </div>
      <div class="contact-line">+1 (555) 010 345
        <svg viewBox="0 0 12 12"><path d="M1 4c0-2 10-2 10 0v1H8V4H4v1H1z" fill="#fff"/><rect x="2.5" y="6" width="7" height="5" fill="#fff"/></svg>
      </div>
      <div class="contact-line">+1 (555) 010 345
        <svg viewBox="0 0 12 12"><rect x="3" y="1" width="6" height="4" fill="none" stroke="#fff"/><rect x="1" y="5" width="10" height="6" fill="#fff"/></svg>
      </div>
    </div>

    <div class="contact-group">
      <div class="contact-line">48 Fenwick Lane, Route 24
        <svg viewBox="0 0 12 12"><path d="M6 11C2 6 2.5 1 6 1s4 5 0 10z" fill="none" stroke="#fff"/><circle cx="6" cy="4.5" r="1.3" fill="#fff"/></svg>
      </div>
      <div class="contact-address">Eastfield, Simla Valley<br>Colorado 80835, USA</div>
    </div>
  </div>
</section>

</body>
</html>
```